A clean crisp business card for a Landscape Construction company. Designed to be easy to read contact/ info and also be appealing/interesting, unlike a traditional business card.

Industry/Entity Type

Landscape Construction

Contact Information for Business Card

Company name : Brambleford Landscape Construction, phone number: (877) 62Vista, website:Bramblefordyards.example, Email, sales@bramblefordyards.example

Requirements
Nice to have
• Luxurious finishes/ details…. Icons or emblems next to contact info
Should not have
• Clipart or general pictures

```html
<!DOCTYPE html>
<html lang="en">
<head>
<meta charset="utf-8">
<title>Brambleford Landscape Construction — Business Card</title>
<link rel="stylesheet" href="https://fonts.googleapis.com/css2?family=Cinzel:wght@500&family=Roboto+Condensed:wght@400;700&display=swap">
<style>
  :root {
    --backdrop: #d9d9db;
    --card: #1d1d1f;
    --card-edge: #2a2a2d;
    --silver: #d6d6d8;
    --silver-dim: #8e8e92;
    --foil-light: #e4e4e6;
    --foil-mid: #9a9a9e;
    --foil-dark: #3a3a3d;
  }
  * { box-sizing: border-box; margin: 0; padding: 0; }
  html, body {
    width: 1200px; height: 800px; overflow: hidden;
    background: var(--backdrop);
    font-family: "Roboto Condensed", Arial, sans-serif;
  }
  .canvas {
    width: 1200px; height: 800px;
    display: flex; flex-direction: column;
    align-items: center; justify-content: center; gap: 56px;
  }
  .card {
    width: 560px; height: 320px;
    background: var(--card);
    border-radius: 22px;
    border: 1px solid var(--card-edge);
    position: relative;
    overflow: hidden;
    color: var(--silver);
  }

  /* Front */
  .card-front {
    display: flex; align-items: center; justify-content: center; gap: 22px;
  }
  .brand-dot {
    width: 26px; height: 26px; border-radius: 50%;
    background: var(--silver);
    flex: none;
  }
  .brand-name {
    font-family: "Cinzel", "Times New Roman", serif;
    font-weight: 500;
    color: var(--silver);
    text-transform: uppercase;
    line-height: 1.05;
  }
  .brand-name-main {
    display: block; font-size: 46px; letter-spacing: 1px;
  }
  .brand-name-sub {
    display: block; font-size: 17px; letter-spacing: 3.4px; margin-top: 6px;
  }

  /* Back */
  .emblem-area {
    position: absolute; left: -40px; bottom: -60px;
    width: 380px; height: 260px;
    border-radius: 50% 50% 0 0;
    background: radial-gradient(ellipse at 35% 55%, var(--foil-light) 0%, var(--foil-mid) 40%, var(--foil-dark) 75%, transparent 100%);
    opacity: .55;
  }
  .contact {
    position: absolute; top: 34px; right: 40px;
    text-align: right; text-transform: uppercase;
  }
  .person-name {
    font-weight: 700; font-size: 22px; letter-spacing: 1.5px; color: var(--silver);
  }
  .person-title {
    font-size: 11px; letter-spacing: 2px; color: var(--silver-dim); margin-bottom: 22px;
  }
  .contact-list { list-style: none; }
  .contact-item {
    display: flex; justify-content: flex-end; align-items: center; gap: 10px;
    font-size: 14px; letter-spacing: .8px; line-height: 22px; color: var(--silver);
  }
  .contact-icon { width: 12px; height: 12px; fill: none; stroke: var(--silver-dim); stroke-width: 1.6; }
</style>
</head>
<body>
<main class="canvas">
  <section class="card card-front" aria-label="Card front">
    <span class="brand-dot"></span>
    <h1 class="brand-name">
      <span class="brand-name-main">Brambleford</span>
      <span class="brand-name-sub">Landscape Construction</span>
    </h1>
  </section>

  <section class="card card-back" aria-label="Card back">
    <div class="emblem-area" role="img" aria-label="Large silver foil brand emblem decoration"></div>
    <div class="contact">
      <p class="person-name">Daniel Hart</p>
      <p class="person-title">President</p>
      <ul class="contact-list">
        <li class="contact-item">(877) 62Vista
          <svg class="contact-icon" viewBox="0 0 12 12"><path d="M3 1 L5 3.5 L4 5 Q5.5 7 7 8 L8.5 7 L11 9 L9.5 11 Q4 10 1 2.5 Z"/></svg>
        </li>
        <li class="contact-item">sales@bramblefordyards.example
          <svg class="contact-icon" viewBox="0 0 12 12"><rect x="1" y="2.5" width="10" height="7"/><path d="M1 2.5 L6 6.5 L11 2.5"/></svg>
        </li>
        <li class="contact-item">Bramblefordyards.example
          <svg class="contact-icon" viewBox="0 0 12 12"><circle cx="6" cy="6" r="5"/><path d="M1 6 H11 M6 1 Q3 6 6 11 Q9 6 6 1"/></svg>
        </li>
      </ul>
    </div>
  </section>
</main>
</body>
</html>
```